Marlowby Services Website Design

We have most content but require a professional design. We have a logo already and will need it utilized along with several of the photos from the attached documentation.
First page should have our mission and Vision and the synapsis provided in the word document. Visitors will be prompted to select from one of our 3 divisions from this page.
Each division will have the same list of tabs : About, Services, Safety, Careers and Contact.
Photos on each divisions page should be representative of the divisions offerings. The word doc attached contains the requested content and we are open to edits that would complement and fill the website.
I like the Quorvane site www.quorvane.example - they are our competition so cant be modeled directly after this.
Please include prompts to request quote at each service page. align the format of the geotechnical page to the other 2 divisions.
I used chat gpt for some of the content so will need it optimized for SCO.

```html
<!DOCTYPE html>
<html lang="en">
<head>
<meta charset="utf-8">
<title>Marlowby Services</title>
<link href="https://fonts.googleapis.com/css2?family=Russo+One&family=Roboto:wght@400;500&display=swap" rel="stylesheet">
<style>
:root{
  --red:#ee1c25;
  --red-dark:#c8161e;
  --ink:#111111;
  --grey-text:#6b6b6b;
  --panel:#f5f3f4;
  --white:#ffffff;
  --black:#000000;
}
*{margin:0;padding:0;box-sizing:border-box}
html,body{width:1200px;height:3324px;overflow:hidden}
body{position:relative;background:var(--white);font-family:"Roboto",Arial,sans-serif;color:var(--ink)}
.abs{position:absolute}
.backdrop{position:absolute;left:0;top:0;width:1200px;height:3324px}

/* header */
.site-header{position:absolute;left:0;top:0;width:1200px;height:66px;background:var(--red)}
.brand{position:absolute;font-family:"Russo One",sans-serif;letter-spacing:2px}
.site-header .brand{left:133px;top:15px;font-size:28px;color:var(--white)}
.main-nav{position:absolute;top:22px;left:0;width:1200px;height:20px}
.main-nav a{position:absolute;color:var(--white);text-decoration:none;font-size:14px;font-weight:500}

/* hero */
.hero-copy{position:absolute;left:111px;top:250px;width:400px}
.eyebrow{font-size:14px;font-weight:500;letter-spacing:.3px}
.hero-title{font-family:"Russo One",sans-serif;font-size:48px;color:var(--red);margin-top:14px;letter-spacing:1px;line-height:1}
.hero-lead{font-size:15px;line-height:27px;margin-top:22px;font-weight:500}
.btn{position:absolute;display:flex;align-items:center;justify-content:center;gap:9px;height:44px;border-radius:22px;background:var(--red);color:var(--white);font-size:16px;font-weight:500;text-decoration:none;box-shadow:0 3px 8px rgba(0,0,0,.15)}
.btn svg{width:15px;height:15px}
.hero-copy .btn{left:1px;top:217px;width:168px}
.play{position:absolute;left:812px;top:270px;width:46px;height:46px;border-radius:50%;background:var(--white);display:flex;align-items:center;justify-content:center;box-shadow:0 2px 8px rgba(0,0,0,.25)}

/* headings */
.section-title{position:absolute;font-family:"Russo One",sans-serif;font-size:36px;letter-spacing:1px;color:var(--ink);white-space:nowrap}
.section-title span{color:var(--red)}
.rule{position:absolute;height:4px;width:93px}
.rule::before{content:"";position:absolute;left:0;top:-2px;width:8px;height:8px;border-radius:50%;background:var(--ink)}
.rule::after{content:"";position:absolute;left:4px;top:1px;right:0;height:3px;background:var(--ink)}

.body-copy{position:absolute;font-size:14.5px;line-height:23px;color:var(--grey-text)}

.photo{position:absolute;overflow:hidden}
.round{border-radius:50%}

/* cards */
.card{position:absolute;background:var(--white);box-shadow:0 4px 14px rgba(0,0,0,.09)}
.card .photo{left:4px;top:0;right:4px}
.card-title{position:absolute;left:0;right:0;text-align:center;font-size:24px;font-weight:500;line-height:30px;color:var(--ink)}
.card-title.caps{font-size:16px;text-transform:uppercase}
.card .btn{left:50%;margin-left:-84px;width:168px}

.arrow{position:absolute;width:40px;height:40px;border-radius:50%;background:var(--red);display:flex;align-items:center;justify-content:center}

/* footer */
.footer-nav a{position:absolute;top:3086px;color:var(--white);font-size:14px;font-weight:500;text-decoration:none}
.social{position:absolute;left:1065px;top:3086px;width:20px;height:20px;border:2px solid var(--white);border-radius:3px}
.footer-col{position:absolute;top:3186px;color:var(--white);font-size:14px;line-height:23px}
.footer-col h4{font-size:14px;font-weight:500;margin-bottom:12px}
.footer .brand{left:116px;top:3188px;font-size:30px;color:var(--red)}
.copyright{position:absolute;left:115px;top:3246px;font-size:12.5px;color:var(--white)}
</style>
</head>
<body>

<svg class="backdrop" viewBox="0 0 1200 3324" aria-hidden="true">
  <defs>
    <linearGradient id="hero-fill" x1="0" y1="0" x2="0" y2="1">
      <stop offset="0" stop-color="#ffffff"/>
      <stop offset=".12" stop-color="#d9dbd6"/>
      <stop offset=".5" stop-color="#9aa08f"/>
      <stop offset="1" stop-color="#6c7263"/>
    </linearGradient>
    <linearGradient id="turbine-fill" x1="0" y1="0" x2="1" y2="1">
      <stop offset="0" stop-color="#f2f2f2"/>
      <stop offset="1" stop-color="#cfcfcf"/>
    </linearGradient>
  </defs>
  <!-- vision / mission soft panel -->
  <rect x="55" y="700" width="810" height="740" rx="30" fill="#fbf9fa"/>
  <!-- hero -->
  <path role="img" aria-label="Aerial view of a prairie town with a service lift truck raising a company sign" d="M0,140 H1200 V600 C900,620 620,720 360,718 C200,716 80,680 0,625 Z" fill="url(#hero-fill)"/>
  <path d="M0,625 C80,680 200,716 360,718 C620,720 900,620 1200,600 L1200,590 C900,606 620,704 360,704 C210,704 90,676 0,618 Z" fill="var(--red)"/>
  <!-- turbine -->
  <path role="img" aria-label="Technician on rope access working on a wind turbine nacelle" d="M0,660 C90,700 220,720 330,716 L330,1000 C250,1060 160,1110 60,1112 L0,1112 Z" fill="url(#turbine-fill)"/>
  <!-- red wave under mission -->
  <path d="M70,1588 C400,1600 700,1470 920,1465 C1050,1462 1140,1510 1185,1550 C1120,1518 1040,1482 920,1482 C700,1486 400,1598 70,1588 Z" fill="var(--red)"/>
  <!-- services panel -->
  <path d="M0,2210 C200,2320 500,2270 800,2200 C950,2168 1060,2165 1200,2168 V2960 H0 Z" fill="var(--panel)"/>
  <path d="M0,2210 C200,2320 500,2270 800,2200 C950,2168 1060,2165 1130,2168 C1060,2172 950,2182 800,2214 C500,2288 200,2338 0,2220 Z" fill="var(--red)"/>
  <!-- footer -->
  <path d="M0,2915 C200,3015 450,3010 700,2960 C900,2915 1050,2884 1200,2880 V3324 H0 Z" fill="var(--black)"/>
  <path d="M0,2915 C200,3015 450,3010 700,2960 C760,2948 820,2936 880,2926 C820,2944 760,2962 700,2976 C450,3032 200,3030 0,2928 Z" fill="var(--red)"/>
</svg>

<header class="site-header">
  <div class="brand">MARLOWBY</div>
  <nav class="main-nav">
    <a style="left:442px">Home</a>
    <a style="left:550px">About</a>
    <a style="left:658px">Services</a>
    <a style="left:783px">Safety</a>
    <a style="left:893px">Careers</a>
    <a style="left:1013px">Contact us</a>
  </nav>
</header>

<section class="hero-copy">
  <p class="eyebrow">WELCOME TO</p>
  <h1 class="hero-title">MARLOWBY</h1>
  <p class="hero-lead">Delivering safe, reliable aerial access and maintenance services to Oil&amp;Gas, Construction, Utility, &amp; Renewable energy industries.</p>
  <a class="btn">Our Services
    <svg viewBox="0 0 16 16"><circle cx="8" cy="8" r="8" fill="#fff"/><path d="M4 8h7M8 5l3 3-3 3" stroke="var(--red)" stroke-width="2" fill="none"/></svg>
  </a>
</section>
<div class="play"><svg width="14" height="16" viewBox="0 0 14 16"><path d="M2 1l11 7-11 7z" fill="#111"/></svg></div>

<!-- vision -->
<div class="photo round" role="img" aria-label="Offshore drilling platform and support vessel at sea" style="left:698px;top:666px;width:386px;height:386px;background:radial-gradient(circle at 50% 25%,#dfeaf3 0,#8fb4d0 22%,#1f5e8c 45%,#0f3e63 100%)"></div>
<h2 class="section-title" style="left:404px;top:804px">OUR <span>VISION</span></h2>
<div class="rule" style="left:404px;top:857px"></div>
<p class="body-copy" style="left:404px;top:888px;width:260px">To be the leading provider of aerial access, geotechnical drilling, and service solutions, setting the standard for excellence in safety, efficiency, and environmental stewardship.</p>

<!-- mission -->
<div class="photo round" role="img" aria-label="Company aerial lift truck parked on a prairie field" style="left:114px;top:1065px;width:386px;height:386px;background:linear-gradient(180deg,#8e8a6e 0,#a9a48a 30%,#dcdcdc 55%,#6f7070 100%)"></div>
<h2 class="section-title" style="left:535px;top:1151px">OUR <span>MISSION</span></h2>
<div class="rule" style="left:535px;top:1205px"></div>
<p class="body-copy" style="left:535px;top:1236px;width:552px">At Marlowby, our mission is to deliver unparalleled aerial access, geotechnical drilling, and service and maintenance solutions, consistently exceeding our clients' expectations. We strive to achieve this by investing in cutting-edge technology, fostering a culture of safety and continuous improvement, and prioritizing environmental sustainability. Through collaboration, integrity, and dedication, we aim to contribute to the success of our clients while maintaining the highest standards of quality and professionalism.</p>

<!-- divisions -->
<h2 class="section-title" style="left:434px;top:1620px">SELECT <span>DIVISION</span></h2>
<div class="rule" style="left:435px;top:1676px"></div>

<article class="card" style="left:112px;top:1784px;width:305px;height:374px">
  <div class="photo" role="img" aria-label="Aerial lift working on a multi-storey building facade" style="height:266px;background:linear-gradient(160deg,#9fb6cc 0,#d9d9d4 45%,#4c4a42 100%)"></div>
  <h3 class="card-title" style="top:292px">Aerial Access</h3>
  <a class="btn" style="top:348px">View More <svg viewBox="0 0 16 16"><circle cx="8" cy="8" r="8" fill="#fff"/><path d="M4 8h7M8 5l3 3-3 3" stroke="var(--red)" stroke-width="2" fill="none"/></svg></a>
</article>

<article class="card" style="left:445px;top:1733px;width:306px;height:379px">
  <div class="photo" role="img" aria-label="Geotechnical drilling rig mast against blue sky" style="height:272px;background:linear-gradient(180deg,#4d86c8 0,#8fb7e0 70%,#c98a2a 100%)"></div>
  <h3 class="card-title" style="top:294px">Geotechnical Drilling</h3>
  <a class="btn" style="top:352px">View More <svg viewBox="0 0 16 16"><circle cx="8" cy="8" r="8" fill="#fff"/><path d="M4 8h7M8 5l3 3-3 3" stroke="var(--red)" stroke-width="2" fill="none"/></svg></a>
</article>

<article class="card" style="left:779px;top:1704px;width:306px;height:377px">
  <div class="photo" role="img" aria-label="Rope access technician standing on a wind turbine above forest" style="height:272px;background:linear-gradient(180deg,#6f9fd0 0,#b7cde0 40%,#3e5a3a 70%,#e8e8e8 100%)"></div>
  <h3 class="card-title" style="top:284px">Renewable Energy<br>Services</h3>
  <a class="btn" style="top:352px">View More <svg viewBox="0 0 16 16"><circle cx="8" cy="8" r="8" fill="#fff"/><path d="M4 8h7M8 5l3 3-3 3" stroke="var(--red)" stroke-width="2" fill="none"/></svg></a>
</article>

<!-- services -->
<h2 class="section-title" style="left:456px;top:2342px">OUR <span>SERVICES</span></h2>
<div class="rule" style="left:458px;top:2396px"></div>

<div class="arrow" style="left:52px;top:2636px"><svg width="10" height="12" viewBox="0 0 10 12"><path d="M7 1L2 6l5 5" stroke="#fff" stroke-width="1.6" fill="none"/></svg></div>
<div class="arrow" style="left:1106px;top:2524px"><svg width="10" height="12" viewBox="0 0 10 12"><path d="M3 1l5 5-5 5" stroke="#fff" stroke-width="1.6" fill="none"/></svg></div>

<article class="card" style="left:112px;top:2494px;width:305px;height:355px">
  <div class="photo" role="img" aria-label="Two workers on a solar panel array under blue sky" style="left:0;right:0;height:271px;background:linear-gradient(180deg,#4f8fd0 0,#c9dcee 45%,#6d7f96 75%,#2e4560 100%)"></div>
  <h3 class="card-title caps" style="top:288px">Renewable Energy Industries.</h3>
  <a class="btn" style="top:334px">View More <svg viewBox="0 0 16 16"><circle cx="8" cy="8" r="8" fill="#fff"/><path d="M4 8h7M8 5l3 3-3 3" stroke="var(--red)" stroke-width="2" fill="none"/></svg></a>
</article>

<article class="card" style="left:445px;top:2446px;width:306px;height:355px">
  <div class="photo" role="img" aria-label="White oil and gas storage tanks with tanker truck" style="left:0;right:0;height:271px;background:linear-gradient(180deg,#f3f5f7 0,#dfe3e8 60%,#9aa0a6 100%)"></div>
  <h3 class="card-title caps" style="top:288px">Maintenance Services to Oil&amp;Gas</h3>
  <a class="btn" style="top:334px">View More <svg viewBox="0 0 16 16"><circle cx="8" cy="8" r="8" fill="#fff"/><path d="M4 8h7M8 5l3 3-3 3" stroke="var(--red)" stroke-width="2" fill="none"/></svg></a>
</article>

<article class="card" style="left:779px;top:2416px;width:306px;height:355px">
  <div class="photo" role="img" aria-label="Construction site with crane and crew in safety vests" style="left:0;right:0;height:273px;background:linear-gradient(180deg,#9aa7b4 0,#e7dfd0 40%,#c9ccce 70%,#8b8f92 100%)"></div>
  <h3 class="card-title caps" style="top:290px">Construction</h3>
  <a class="btn" style="top:336px">View More <svg viewBox="0 0 16 16"><circle cx="8" cy="8" r="8" fill="#fff"/><path d="M4 8h7M8 5l3 3-3 3" stroke="var(--red)" stroke-width="2" fill="none"/></svg></a>
</article>

<!-- footer -->
<footer class="footer">
  <nav class="footer-nav">
    <a style="left:350px">Home</a>
    <a style="left:458px">About</a>
    <a style="left:566px">Services</a>
    <a style="left:690px">Safety</a>
    <a style="left:801px">Careers</a>
    <a style="left:921px">Contact us</a>
  </nav>
  <div class="social" aria-label="Social profile"></div>
  <div class="brand">MARLOWBY</div>
  <p class="copyright">Copyright@Marlowby.All Rights Reserved</p>
  <div class="footer-col" style="left:426px"><h4>Location</h4>27 Ridgeline Avenue Halden Falls<br>AB T0X-4B1</div>
  <div class="footer-col" style="left:710px"><h4>Email</h4>info@marlowbyservices.example</div>
  <div class="footer-col" style="left:990px"><h4>Phone</h4>&nbsp;(555) 010-4372</div>
</footer>

</body>
</html>
```